Quennard Capital LLC

Need Professional Business cards for New Investment Fund

Target Market(s)

High Quality investors

Industry/Entity Type

Financial

Contact Information for Business Card

Phone Number +1 555 284 6190
Name Lukas Varenko
Title Fund Manager
email lv@FundQuennard.com
Website www.FundQuennard.com

Colors

Designer to choose colors to be used in the design.

Requirements
Must have
• Must have our Logo and all of the above. Must be made so lettering and loge can be raised

```html
<!DOCTYPE html>
<html lang="en">
<head>
<meta charset="utf-8">
<title>Quennard Capital LLC — Business Card</title>
<link rel="stylesheet" href="https://fonts.googleapis.com/css2?family=Archivo:wght@400;500;700&display=swap">
<style>
  :root {
    --backdrop: #ddd3cb;
    --card-front: #0b0b09;
    --card-back: #252523;
    --accent: #86e03a;
    --text-light: #f2f2ee;
  }
  * { margin: 0; padding: 0; box-sizing: border-box; }
  html, body { width: 1200px; height: 988px; overflow: hidden; }
  body {
    background: var(--backdrop);
    font-family: "Archivo", Arial, sans-serif;
    display: flex;
    align-items: center;
    justify-content: center;
    gap: 80px;
  }
  .card {
    position: relative;
    width: 372px;
    height: 620px;
    border-bottom: 9px solid var(--accent);
    overflow: hidden;
  }
  .card--front { background: var(--card-front); }
  .card--back { background: var(--card-back); }

  .brand {
    position: absolute;
    display: flex;
    align-items: center;
    gap: 10px;
    color: var(--accent);
    font-weight: 700;
    letter-spacing: 2px;
    text-transform: uppercase;
    white-space: nowrap;
  }
  .brand__square { background: var(--accent); flex: none; }
  .card--front .brand { left: 60px; top: 120px; font-size: 20px; }
  .card--front .brand__square { width: 18px; height: 18px; }
  .card--back .brand {
    left: 0; right: 0; top: 230px;
    justify-content: center;
    font-size: 38px;
    gap: 14px;
  }
  .card--back .brand__square { width: 30px; height: 30px; }

  .identity { position: absolute; left: 44px; right: 40px; top: 318px; }
  .identity__name {
    color: var(--accent);
    font-weight: 700;
    font-size: 29px;
    letter-spacing: 2.5px;
    white-space: nowrap;
  }
  .identity__title {
    color: var(--text-light);
    font-size: 17px;
    letter-spacing: 2px;
    margin: 4px 0 0 100px;
  }
  .divider {
    position: absolute;
    left: 72px; right: 40px; top: 402px;
    height: 2px;
    background: var(--accent);
  }
  .contacts {
    position: absolute;
    left: 64px; top: 432px;
    list-style: none;
  }
  .contacts__item {
    display: flex;
    align-items: center;
    gap: 14px;
    height: 50px;
    color: var(--text-light);
    font-size: 15px;
    letter-spacing: 1.5px;
    white-space: nowrap;
  }
  .contacts__icon { width: 28px; height: 28px; flex: none; }
  .contacts__icon * { fill: none; stroke: var(--accent); stroke-width: 2; }
</style>
</head>
<body>
  <section class="card card--front" aria-label="Business card front">
    <div class="brand"><span class="brand__square"></span>Quennard</div>
    <div class="identity">
      <p class="identity__name">Lukas Varenko</p>
      <p class="identity__title">Fund Manager</p>
    </div>
    <div class="divider"></div>
    <ul class="contacts">
      <li class="contacts__item">
        <svg class="contacts__icon" viewBox="0 0 30 30" aria-hidden="true">
          <path d="M6 9c0-2 2-3 3-3l2 4-2 2c1 3 4 6 7 7l2-2 4 2c0 1-1 3-3 3C12 22 6 15 6 9z"/>
        </svg>
        +1 555 284 6190
      </li>
      <li class="contacts__item">
        <svg class="contacts__icon" viewBox="0 0 30 30" aria-hidden="true">
          <circle cx="15" cy="15" r="12"/>
          <circle cx="15" cy="15" r="4.5"/>
          <path d="M19.5 11v6c0 2 3 2 3-1"/>
        </svg>
        lv@FundQuennard.com
      </li>
      <li class="contacts__item">
        <svg class="contacts__icon" viewBox="0 0 30 30" aria-hidden="true">
          <circle cx="15" cy="15" r="12"/>
          <ellipse cx="15" cy="15" rx="5" ry="12"/>
          <path d="M3 15h24M5 9h20M5 21h20"/>
        </svg>
        www.FundQuennard.com
      </li>
    </ul>
  </section>

  <section class="card card--back" aria-label="Business card back">
    <div class="brand"><span class="brand__square"></span>Quennard</div>
  </section>
</body>
</html>
```